KBT Business Cards

We require business cards for our business. We would like a matte black back to the card, with our logo centred in the middle. The front side of the card is open to design.

Target Market(s)

Clients looking for legal services (professional)

Industry/Entity Type

Legal

Contact Information for Business Card

Doran Kelbrath
Partner
Mobile: 0461 738 524
Email: doran@kbtlaw.co
Website: www.kbtlaw.co
Level 3, 118 Wendmore Street
Sydney NSW 2000

Font styles to use
Other font styles liked:
• Avenir

Colors
f04a50
ffffff
1b1b1b

Requirements
Must have
• Black back with logo included in the centre of the card.
• Our font is Avenir.

```html
<!DOCTYPE html>
<html lang="en">
<head>
<meta charset="utf-8">
<title>KBT Legal Business Cards</title>
<link href="https://fonts.googleapis.com/css2?family=Source+Sans+3:wght@400;600;700&display=swap" rel="stylesheet">
<style>
  :root {
    --crimson: #b8203f;
    --ink: #231f20;
    --text: #333333;
    --paper: #ffffff;
    --font: "Source Sans 3", "Avenir", sans-serif;
  }
  * { margin: 0; padding: 0; box-sizing: border-box; }
  html, body { width: 1200px; height: 1200px; overflow: hidden; background: var(--paper); }
  body { position: relative; font-family: var(--font); }

  .card {
    position: absolute;
    width: 739px;
    height: 421px;
    box-shadow: 0 1px 6px rgba(0,0,0,0.22);
    overflow: hidden;
  }
  .card-front { left: 231px; top: 157px; background: var(--paper); }
  .card-back { left: 230px; top: 633px; background: var(--ink); }

  /* Firm name lockup */
  .wordmark { position: absolute; display: flex; align-items: center; }
  .wordmark-square { background: var(--crimson); flex: none; }
  .wordmark-name { font-weight: 700; text-transform: uppercase; letter-spacing: 0.2px; }
  .wordmark-name span { display: block; }

  .card-front .wordmark { right: 30px; top: 50px; gap: 18px; }
  .card-front .wordmark-square { width: 30px; height: 30px; }
  .card-front .wordmark-name { color: var(--ink); font-size: 27px; line-height: 28px; }

  .card-back .wordmark { left: 0; right: 0; top: 142px; justify-content: center; gap: 30px; }
  .card-back .wordmark-square { width: 46px; height: 46px; }
  .card-back .wordmark-name { color: var(--paper); font-size: 43px; line-height: 43px; }

  /* Identity */
  .accent-bar { position: absolute; left: 0; top: 215px; width: 10px; height: 45px; background: var(--crimson); }
  .person-name { position: absolute; left: 32px; top: 209px; font-size: 25px; font-weight: 700; color: var(--crimson); }
  .person-role { position: absolute; left: 32px; top: 243px; font-size: 18px; color: var(--text); }
  .rule { position: absolute; left: 103px; right: 32px; top: 255px; height: 1px; background: var(--crimson); }

  /* Contact details */
  .contacts { position: absolute; left: 31px; top: 289px; list-style: none; }
  .contacts li { display: flex; align-items: center; gap: 9px; height: 27px; font-size: 18px; color: var(--text); }
  .contacts svg { width: 14px; height: 14px; flex: none; fill: var(--crimson); }

  .address { position: absolute; right: 32px; top: 322px; text-align: right; font-size: 18px; line-height: 21px; color: var(--text); font-style: normal; }

  /* Plain footer bands */
  .footer-line { position: absolute; left: 0; right: 0; bottom: 28px; height: 4px; background: var(--ink); }
  .footer-band { position: absolute; left: 0; right: 0; bottom: 0; height: 24px; background: var(--crimson); }
</style>
</head>
<body>

<section class="card card-front" aria-label="Card front">
  <div class="wordmark">
    <div class="wordmark-square"></div>
    <div class="wordmark-name"><span>Kelbrath</span><span>Barrow Tate</span><span>Legal</span></div>
  </div>

  <div class="accent-bar"></div>
  <h1 class="person-name">Doran Kelbrath</h1>
  <p class="person-role">Partner</p>
  <div class="rule"></div>

  <ul class="contacts">
    <li>
      <svg viewBox="0 0 16 16" aria-hidden="true"><path d="M3.5 1 6 3.5 4.7 5.6c.9 2 2.7 3.8 4.7 4.7L11.5 9 14 11.5l-1.6 2.6C7 13.8 2.2 9 1.9 3.6z"/></svg>
      0461 738 524
    </li>
    <li>
      <svg viewBox="0 0 16 16" aria-hidden="true"><path d="M1 3h14v10H1zM2.5 4.5v.3L8 9l5.5-4.2v-.3zM2.5 6.6v5h11v-5L8 10.8z"/></svg>
      doran@kbtlaw.co
    </li>
    <li>
      <svg viewBox="0 0 16 16" aria-hidden="true"><circle cx="8" cy="8" r="7"/><path d="M1.5 8h13M8 1.5c-2.5 2.5-2.5 10.5 0 13M8 1.5c2.5 2.5 2.5 10.5 0 13" stroke="#fff" stroke-width="1.1" fill="none"/></svg>
      www.kbtlaw.co
    </li>
  </ul>

  <address class="address">Level 3, 118 Wendmore Street<br>Sydney NSW 2000</address>

  <div class="footer-line"></div>
  <div class="footer-band"></div>
</section>

<section class="card card-back" aria-label="Card back">
  <div class="wordmark">
    <div class="wordmark-square"></div>
    <div class="wordmark-name"><span>Kelbrath</span><span>Barrow Tate</span><span>Legal</span></div>
  </div>
</section>

</body>
</html>
```